Revamp Marketing Website For Video Production Website

need to revamp current website www.kestrelfilmstudio.net
reference sites www.vantora.net & http://layoutcrate.net/kestrel/
Use all current content on current kestrel website. I want a revamped modenr look. Sometbing that wows customers.
reference site www.vantora.net
Target Market(s)
business owners
Industry/Entity Type
Video Production
Number of Pages Required
5+ page
Colors
Designer to choose colors to be used in the design.
Requirements
Must have
- need to revamp current website www.kestrelfilmstudio.net
- reference sites www.vantora.net & http://layoutcrate.net/kestrel/
- Use all current content on current kestrel website. I want a revamped modenr look. Sometbing that wows customers.
- reference site www.vantora.net
Nice to have
Should not have

```html
<!DOCTYPE html>
<html lang="en">
<head>
<meta charset="utf-8">
<title>Kestrel – Marketing Videos Made For You</title>
<link href="https://fonts.googleapis.com/css2?family=Lato:wght@400;700;900&display=swap" rel="stylesheet">
<style>
:root{
  --blue:#1a9ee0;
  --blue-dark:#1487c4;
  --ink:#222;
  --text:#333;
  --muted:#555;
  --white:#fff;
  --black:#0b0b0b;
  --grey-band:#dfe2e5;
  --teal:#14908f;
  --teal-deep:#1d4f5e;
  --navy:#1e2c3a;
  --slate:#3e5b83;
  --slate-deep:#2b3a4c;
  --night:#1a222c;
}
*{box-sizing:border-box;margin:0;padding:0}
html,body{width:1200px;height:4036px;overflow:hidden;background:var(--white)}
body{font-family:"Lato",Arial,sans-serif;color:var(--text)}
.page{position:relative;width:1200px;height:4036px;overflow:hidden}
.abs{position:absolute}
.center-text{text-align:center}

/* hero */
.hero{position:absolute;left:0;top:0;width:1200px;height:600px;
  background:radial-gradient(ellipse at 50% 55%,#2d4a12 0%,#0f1a10 35%,#050607 70%),#050607}
.hero-glow{position:absolute;left:0;top:250px;width:1200px;height:140px;
  background:linear-gradient(90deg,rgba(30,160,200,.35),rgba(220,220,60,.45) 40%,rgba(120,200,60,.35) 70%,rgba(20,120,200,.3));filter:blur(30px)}
.hero-cut{position:absolute;left:0;top:520px}
.logo{position:absolute;left:75px;top:30px;color:var(--white)}
.logo-name{font-size:38px;font-weight:900;letter-spacing:4px;line-height:1}
.logo-tag{font-size:11px;letter-spacing:1.6px;margin-top:6px}
.nav{position:absolute;top:58px;left:0;width:1200px;font-size:14px;color:var(--white)}
.nav span{position:absolute;white-space:nowrap}
.nav .active{border-bottom:2px solid var(--blue);padding-bottom:6px}
.nav .login{color:var(--blue);font-weight:700}
.hero-title{position:absolute;top:204px;width:1200px;font-size:30px;color:var(--white);letter-spacing:1px}
.hero-sub{position:absolute;top:256px;width:1200px;font-size:24px;color:var(--white)}
.btn-hero{position:absolute;left:444px;top:322px;width:315px;height:76px;background:var(--blue);color:var(--white);
  border-radius:4px;font-size:15px;line-height:23px;padding-top:15px;text-align:center}
.hero-note{position:absolute;top:438px;width:1200px;font-size:17px;font-weight:700;color:#d8d8d8;line-height:30px;letter-spacing:.5px}
.socials{position:absolute;top:520px;left:365px;display:flex;gap:34px}
.socials i{width:22px;height:22px;border-radius:50%;background:var(--blue);display:block}
.arrow{position:absolute;top:275px}

/* headings */
.h-section{position:absolute;width:1200px;text-align:center;color:var(--blue);font-weight:900;font-size:30px;letter-spacing:.5px}
.lead{position:absolute;width:1200px;text-align:center;font-size:17px;line-height:25px;color:var(--ink)}
.btn{position:absolute;background:var(--blue);color:var(--white);font-weight:700;text-align:center;border-radius:5px}
.btn-lg{width:162px;height:54px;line-height:54px;font-size:20px}
.btn-sm{width:107px;height:36px;line-height:36px;font-size:13px;border-radius:4px}

/* examples */
.thumb{position:absolute;top:936px;width:333px;height:213px}
.thumb-1{left:73px;background:linear-gradient(180deg,#1b2a55,#2c3f78 55%,#0b1024)}
.thumb-2{left:433px;background:linear-gradient(180deg,#f0a340,#c04a14 55%,#1a0c06)}
.thumb-3{left:794px;background:linear-gradient(120deg,#e8c088,#8a4a20 50%,#2a120a)}
.play{position:absolute;left:148px;top:89px;width:38px;height:28px;border:2px solid rgba(255,255,255,.85);border-radius:6px}
.play:after{content:"";position:absolute;left:13px;top:6px;border-left:11px solid rgba(255,255,255,.85);border-top:6px solid transparent;border-bottom:6px solid transparent}
.caption{position:absolute;top:1162px;width:333px;text-align:center;font-size:22px;color:var(--ink)}

/* features */
.features{position:absolute;left:0;top:1350px;width:1200px;height:762px;
  background:linear-gradient(135deg,#eef0f2,#d3d7db 50%,#e6e8ea)}
.hub{position:absolute;left:471px;top:1577px;width:252px;height:252px;border-radius:50%;background:var(--white);
  box-shadow:0 12px 30px rgba(0,0,0,.25)}
.hub-core{position:absolute;left:22px;top:22px;width:208px;height:208px;border-radius:50%;background:var(--black);color:var(--white);text-align:center;padding-top:82px}
.hub-core .logo-name{font-size:30px;letter-spacing:3px}
.hub-core .logo-tag{font-size:8px;letter-spacing:1px}
.pill{position:absolute;height:110px;border-radius:55px;color:var(--white);box-shadow:0 8px 16px rgba(0,0,0,.22)}
.pill-title{font-size:13px;font-weight:900;line-height:15px}
.pill-text{font-size:11px;line-height:14px;margin-top:3px;opacity:.92}
.pill .icon{position:absolute;top:14px;width:82px;height:82px;border-radius:50%;background:var(--white);display:flex;align-items:center;justify-content:center}
.pill-left .copy{position:absolute;left:30px;top:24px;width:170px}
.pill-left .icon{right:14px}
.pill-right .copy{position:absolute;left:112px;top:18px;width:160px}
.pill-right .icon{left:14px}
.node{position:absolute;width:22px;height:22px;border-radius:50%;border:4px solid var(--teal-deep);background:var(--white)}

/* sizes */
.photo{position:absolute;box-shadow:0 6px 16px rgba(0,0,0,.2);border:5px solid var(--white)}
.size-title{position:absolute;width:400px;text-align:center;font-size:26px;font-weight:700;color:var(--ink);letter-spacing:.5px}
.size-text{position:absolute;width:400px;text-align:center;font-size:15px;line-height:25px;color:var(--ink)}

/* footer */
.footer{position:absolute;left:0;top:3605px;width:1200px;height:431px;background:var(--black);color:var(--white)}
.footer .logo{top:80px}
.foot-strap{position:absolute;left:75px;top:145px;font-size:23px;font-weight:900;line-height:35px}
.foot-copy{position:absolute;left:75px;top:212px;width:400px;font-size:17px;line-height:45px}
.foot-head{position:absolute;top:52px;font-size:21px;font-weight:900}
.foot-list{position:absolute;top:100px;list-style:none;font-size:16px;line-height:33px}
.foot-list li{display:flex;align-items:center;gap:14px}
.foot-list .chev{font-size:12px}
.foot-list .dot{width:14px;height:14px;border-radius:50%;background:var(--white);display:inline-block}
.chat{position:absolute;left:1058px;top:310px;width:58px;height:58px;border-radius:50%;background:var(--white);box-shadow:0 4px 10px rgba(0,0,0,.4)}
.chat:after{content:"";position:absolute;left:13px;top:13px;width:32px;height:32px;border-radius:50%;background:var(--blue)}
.foot-mark{position:absolute;left:1128px;top:378px;font-size:11px}
.copyright{position:absolute;top:383px;width:1200px;text-align:center;font-size:14px}
</style>
</head>
<body>
<div class="page">

  <header class="hero" role="img" aria-label="Dark background with glowing streaks of light">
    <div class="hero-glow"></div>
  </header>
  <svg class="hero-cut" width="1200" height="80" viewBox="0 0 1200 80"><polygon points="0,72 1200,18 1200,80 0,80" fill="#fff"/></svg>

  <div class="logo"><div class="logo-name">KESTREL</div><div class="logo-tag">MARKETING VIDEOS MADE FOR YOU</div></div>
  <nav class="nav">
    <span class="active" style="left:336px">HOME</span>
    <span style="left:417px">HOW IT WORKS</span>
    <span style="left:565px">EXAMPLES</span>
    <span style="left:678px">FAQ</span>
    <span style="left:745px">CONTACT US</span>
    <span style="left:874px">PRICING</span>
    <span class="login" style="left:985px">LOGIN</span>
    <span style="left:1045px">|</span>
    <span style="left:1067px">SIGN UP</span>
  </nav>

  <svg class="arrow" style="left:130px" width="20" height="28" viewBox="0 0 20 28"><path d="M15 4 L5 14 L15 24" stroke="#fff" stroke-width="4" fill="none"/></svg>
  <svg class="arrow" style="left:1050px" width="20" height="28" viewBox="0 0 20 28"><path d="M5 4 L15 14 L5 24" stroke="#fff" stroke-width="4" fill="none"/></svg>

  <h1 class="hero-title center-text">ATTENTION GRABBING "VIRAL" TYPE VIDEO ADS</h1>
  <p class="hero-sub center-text">All Delivered in 24 Hours!</p>
  <div class="btn-hero">Get One FREE Video Mockup Now<br>No Purchase necessary</div>
  <p class="hero-note center-text">WE CREATE AWARD WINNING PROMOTIONAL<br>MARKETING VIDEOS TO USE ALL OVER THE WEB</p>
  <div class="socials" aria-label="Social links"><i></i><i></i><i></i><i></i><i></i><i></i><i></i><i></i></div>

  <h2 class="h-section" style="top:700px">PROMOTE ANYTHING ANYWHERE ON THE WEB.</h2>
  <p class="lead" style="top:752px">For less than the cost and time of a DIY video maker software, we will make you world class promotional<br>marketing videos that will make your business stand out from the competition.</p>

  <h2 class="h-section" style="top:862px">OUR EXAMPLES</h2>
  <div class="thumb thumb-1" role="img" aria-label="Illuminated palace reflected in a lake at dusk"><div class="play"></div></div>
  <div class="thumb thumb-2" role="img" aria-label="Photographer silhouetted against a sunset"><div class="play"></div></div>
  <div class="thumb thumb-3" role="img" aria-label="Person writing at a desk in warm light"><div class="play"></div></div>
  <div class="caption" style="left:73px">Tour Places Promo1</div>
  <div class="caption" style="left:433px">Tour Places Promo2</div>
  <div class="caption" style="left:794px">Tour Places Promo3</div>
  <div class="btn btn-lg" style="left:519px;top:1229px">More Info</div>

  <section class="features" role="img" aria-label="Soft grey low-poly background"></section>
  <h2 class="h-section" style="top:1400px">OUR FEATURES.</h2>
  <svg class="abs" style="left:387px;top:1493px" width="420" height="420" viewBox="0 0 420 420"><circle cx="210" cy="210" r="206" fill="none" stroke="#444" stroke-width="3" stroke-dasharray="2 7"/></svg>

  <div class="pill pill-left" style="left:148px;top:1492px;width:282px;background:var(--teal)">
    <div class="copy"><div class="pill-title">DONE FOR YOU</div><div class="pill-text">You Don't Lift A Finger!</div></div>
    <div class="icon"><svg width="50" height="50" viewBox="0 0 50 50"><circle cx="25" cy="25" r="23" fill="var(--teal)"/><path d="M14 25 L22 33 L36 17" stroke="#fff" stroke-width="5" fill="none"/></svg></div>
  </div>
  <div class="pill pill-left" style="left:100px;top:1653px;width:304px;background:var(--teal-deep)">
    <div class="copy"><div class="pill-title">PREMIUM CONTENT</div><div class="pill-text">Your Business Will Look Super High-End &amp; Professional</div></div>
    <div class="icon"><svg width="50" height="50" viewBox="0 0 50 50"><circle cx="25" cy="25" r="23" fill="var(--teal-deep)"/><polygon points="25,10 29,21 40,21 31,28 34,39 25,32 16,39 19,28 10,21 21,21" fill="#fff"/></svg></div>
  </div>
  <div class="pill pill-left" style="left:148px;top:1815px;width:282px;background:var(--navy)">
    <div class="copy"><div class="pill-title">FULLY LICENSED TO YOU</div><div class="pill-text">You Own All The Videos To Use Forever - Consider Them Assets!</div></div>
    <div class="icon"><svg width="50" height="50" viewBox="0 0 50 50"><circle cx="25" cy="25" r="23" fill="var(--navy)"/><path d="M25 12 L36 26 H29 V38 H21 V26 H14 Z" fill="#fff"/></svg></div>
  </div>

  <div class="pill pill-right" style="left:775px;top:1492px;width:274px;background:var(--slate)">
    <div class="icon"><svg width="50" height="50" viewBox="0 0 50 50"><circle cx="25" cy="25" r="23" fill="var(--slate)"/><path d="M16 12 H34 L25 25 L34 38 H16 L25 25 Z" fill="#fff"/></svg></div>
    <div class="copy"><div class="pill-title">PERFECT LENGTH FOR MARKETING VIDEOS</div><div class="pill-text">Stand Out From The Crowd With Video Marketing</div></div>
  </div>
  <div class="pill pill-right" style="left:820px;top:1653px;width:272px;background:var(--slate-deep)">
    <div class="icon"><svg width="50" height="50" viewBox="0 0 50 50"><circle cx="25" cy="25" r="23" fill="var(--slate-deep)"/><rect x="13" y="16" width="24" height="16" rx="3" fill="#fff"/><polygon points="22,20 30,24 22,28" fill="var(--slate-deep)"/></svg></div>
    <div class="copy"><div class="pill-title">CHATTERBOX VIDEO COVER</div><div class="pill-text">"Wow" Customers With A Beautiful Designed Chatterbox Cover Video For Your Business</div></div>
  </div>
  <div class="pill pill-right" style="left:775px;top:1815px;width:274px;background:var(--night)">
    <div class="icon"><svg width="50" height="50" viewBox="0 0 50 50"><circle cx="25" cy="25" r="23" fill="var(--night)"/><circle cx="25" cy="25" r="10" fill="none" stroke="#fff" stroke-width="6" stroke-dasharray="5 3"/><circle cx="25" cy="25" r="4" fill="#fff"/></svg></div>
    <div class="copy"><div class="pill-title">BEST SUPPORT</div><div class="pill-text">We Are Available To You At All Times For Any Kind Of Support</div></div>
  </div>

  <span class="node" style="left:437px;top:1536px"></span>
  <span class="node" style="left:408px;top:1697px"></span>
  <span class="node" style="left:437px;top:1859px"></span>
  <span class="node" style="left:741px;top:1536px"></span>
  <span class="node" style="left:770px;top:1697px"></span>
  <span class="node" style="left:741px;top:1859px"></span>

  <div class="hub"><div class="hub-core"><div class="logo-name">KESTREL</div><div class="logo-tag">MARKETING VIDEOS MADE FOR YOU</div></div></div>
  <div class="btn btn-lg" style="left:519px;top:1964px">View More</div>

  <h2 class="h-section" style="top:2188px">VIDEO SIZES AVAILABLE</h2>

  <div class="photo" style="left:137px;top:2324px;width:420px;height:259px;background:linear-gradient(120deg,#5a6470,#c9c5bd 55%,#8a8f96)" role="img" aria-label="Team working together around a laptop in an office"></div>
  <h3 class="size-title" style="left:647px;top:2370px">WIDE SCREEN VIDEOS</h3>
  <p class="size-text" style="left:647px;top:2427px">This size is a standard video size that works best for<br>pretty much anywhere on the web (1080x720) Included<br>with all video purchases</p>
  <div class="btn btn-sm" style="left:794px;top:2523px">View More</div>

  <h3 class="size-title" style="left:136px;top:2706px">SQUARE VIDEOS</h3>
  <p class="size-text" style="left:136px;top:2762px">That work best on CHATTERBOX (Square is 1080<br>X 1080) Convert any video to this size for an<br>additional fee of $39</p>
  <div class="btn btn-sm" style="left:283px;top:2862px">View More</div>
  <div class="photo" style="left:663px;top:2641px;width:183px;height:170px;background:radial-gradient(circle at 50% 55%,#f5b040,#6a2a08 60%,#1a0a04)" role="img" aria-label="Glowing filament light bulb"></div>
  <div class="photo" style="left:852px;top:2641px;width:237px;height:214px;background:linear-gradient(135deg,#d8c8a8,#8c6a48 60%,#3a3a40)" role="img" aria-label="Shop owner handing over a paper bag"></div>
  <div class="photo" style="left:619px;top:2815px;width:231px;height:203px;background:linear-gradient(180deg,#9cc0dc,#7a6a5a 50%,#5a7a40)" role="img" aria-label="Brick house with a front garden"></div>
  <div class="photo" style="left:852px;top:2862px;width:185px;height:156px;background:linear-gradient(135deg,#c8d0c0,#9a1a14 55%,#3a0808)" role="img" aria-label="Glass of red wine"></div>

  <div class="photo" style="left:75px;top:3097px;width:120px;height:345px;background:linear-gradient(180deg,#c8a888,#8a6a58)" role="img" aria-label="Woman smiling outdoors"></div>
  <div class="photo" style="left:460px;top:3120px;width:116px;height:320px;background:linear-gradient(180deg,#a88a70,#5a3a2a)" role="img" aria-label="Woman standing in a city street"></div>
  <div class="photo" style="left:188px;top:3065px;width:282px;height:464px;background:linear-gradient(180deg,#d8c8b0,#a88058 45%,#3a3a48)" role="img" aria-label="Smiling woman holding a phone in a city street"></div>
  <h3 class="size-title" style="left:647px;top:3188px">VERTICAL VIDEOS</h3>
  <p class="size-text" style="left:647px;top:3243px">That work best on STORIES for Chatterbox, Snapframe and<br>Flashchat (1080 X 1920) Convert any video to this size for<br>an additional fee of $39</p>
  <div class="btn btn-sm" style="left:794px;top:3336px">View More</div>

  <footer class="footer">
    <div class="logo"><div class="logo-name">KESTREL</div><div class="logo-tag">MARKETING VIDEOS MADE FOR YOU</div></div>
    <p class="foot-strap">CREATED BY A MARKETER<br>FOR MARKETERS</p>
    <p class="foot-copy">With Kestrel, you simply let us know what you want to promote and we will have your video ad finished as soon as 24 hours!</p>

    <h4 class="foot-head" style="left:543px">QUICK LINK</h4>
    <ul class="foot-list" style="left:548px">
      <li><span class="chev">&gt;</span>How It Works</li>
      <li><span class="chev">&gt;</span>Term Of Service</li>
      <li><span class="chev">&gt;</span>Privacy Policy</li>
      <li><span class="chev">&gt;</span>Cookies Policy</li>
    </ul>

    <h4 class="foot-head" style="left:888px">FOLLOW US</h4>
    <ul class="foot-list" style="left:888px">
      <li><span class="dot"></span>Chatterbox</li>
      <li><span class="dot"></span>Viewcast</li>
      <li><span class="dot"></span>Chirpline</li>
      <li><span class="dot"></span>Pinspire</li>
      <li><span class="dot"></span>Workfolio</li>
      <li><span class="dot"></span>Orbit Plus</li>
    </ul>

    <div class="chat"></div>
    <span class="foot-mark">M1</span>
    <p class="copyright">© 2019 | www.companyname.com</p>
  </footer>
</div>
</body>
</html>
```